Awesome photographers card for an awesome new business

Double sided business card Black background and silver logo in middle on one side. Details on otherside. please keep it simple

Industry/Entity Type

Photographer

Contact Information for Business Card

Gerald Fenwick
0452817360
GeraldFenwickPhotography47@mailbox.test
www.GeraldFenwickPhotography.test.au
Instagram _Gerald_fenwick

Requirements
Must have
• My logo in Silver
• please use instagram logo instead of "Instagram"

```html
<!DOCTYPE html>
<html lang="en">
<head>
<meta charset="utf-8">
<title>Gerald Fenwick – Business Card</title>
<link href="https://fonts.googleapis.com/css2?family=Source+Sans+3:wght@400;600&display=swap" rel="stylesheet">
<style>
  :root {
    --stage: #000000;
    --card-top: #38383c;
    --card-bottom: #2f2f33;
    --silver: #d4d4d8;
    --text: #e4e4e6;
    --rule: #48484d;
  }
  * { margin: 0; padding: 0; box-sizing: border-box; }
  html, body {
    width: 1200px; height: 900px; overflow: hidden;
    background: var(--stage);
    font-family: "Source Sans 3", "Myriad Pro", sans-serif;
  }
  .stage { position: relative; width: 1200px; height: 900px; }
  .card {
    position: absolute; top: 271px;
    width: 457px; height: 281px; border-radius: 14px;
    background: linear-gradient(180deg, var(--card-top), var(--card-bottom));
  }
  .card--details { left: 137px; }
  .card--brand { left: 627px; }

  .brand-mark {
    position: absolute; display: flex; flex-direction: column; align-items: center;
    color: var(--silver); font-weight: 400; text-align: center; line-height: 1.05;
    white-space: nowrap;
  }
  .brand-ring { border: 2px solid var(--silver); border-radius: 50%; flex: none; }

  .card--details .brand-mark { left: 26px; width: 122px; top: 94px; gap: 8px; font-size: 17px; }
  .card--details .brand-ring { width: 32px; height: 32px; }

  .card--brand .brand-mark { left: 0; right: 0; top: 86px; gap: 12px; font-size: 30px; }
  .card--brand .brand-ring { width: 50px; height: 50px; border-width: 2.5px; }

  .divider {
    position: absolute; left: 153px; top: 84px; width: 1px; height: 126px;
    background: var(--rule);
  }
  .holder {
    position: absolute; left: 169px; top: 82px;
    font-size: 17.5px; font-weight: 600; color: var(--text);
  }
  .contact-list { position: absolute; left: 170px; top: 126px; list-style: none; }
  .contact-item {
    display: flex; align-items: center; gap: 7px;
    height: 19px; font-size: 13.2px; color: var(--text);
  }
  .contact-icon { width: 10px; height: 10px; flex: none; fill: var(--silver); }
</style>
</head>
<body>
<main class="stage">
  <section class="card card--details" aria-label="Card front with contact details">
    <div class="brand-mark"><span class="brand-ring"></span><span>Gerald<br>Fenwick</span></div>
    <div class="divider"></div>
    <h1 class="holder">Gerald Fenwick</h1>
    <ul class="contact-list">
      <li class="contact-item">
        <svg class="contact-icon" viewBox="0 0 10 10"><path d="M2 0.5 L3.6 2.6 L2.8 3.6 Q4 6 6.4 7.2 L7.4 6.4 L9.5 8 L8.4 9.5 Q3.5 9 0.5 1.6 Z"/></svg>
        <span>0452817360</span>
      </li>
      <li class="contact-item">
        <svg class="contact-icon" viewBox="0 0 10 10"><path d="M0.5 2 H9.5 V8.5 H0.5 Z"/><path d="M0.8 2.3 L5 5.6 L9.2 2.3" fill="none" stroke="#333" stroke-width="0.9"/></svg>
        <span>GeraldFenwickPhotography47@mailbox.test</span>
      </li>
      <li class="contact-item">
        <svg class="contact-icon" viewBox="0 0 10 10"><circle cx="5" cy="5" r="4.5"/><path d="M0.5 5 H9.5 M5 0.5 Q2.5 5 5 9.5 M5 0.5 Q7.5 5 5 9.5" fill="none" stroke="#333" stroke-width="0.8"/></svg>
        <span>www.GeraldFenwickPhotography.test.au</span>
      </li>
      <li class="contact-item">
        <svg class="contact-icon" viewBox="0 0 10 10"><rect x="1" y="1" width="8" height="8"/></svg>
        <span>Gerald_fenwick</span>
      </li>
    </ul>
  </section>

  <section class="card card--brand" aria-label="Card back with brand name">
    <div class="brand-mark"><span class="brand-ring"></span><span>Gerald Fenwick</span></div>
  </section>
</main>
</body>
</html>
```